Social Media Graphics - Oakline Push REVISED

Create 6-7 individual social media graphics (square size) to encourage folks to join our online course called:

The Harvest Ledger Circle
How to Launch a Multi-Million Business From Scratch
Sign Up Today!

IMPORTANT: Make the largest and most prominent text on the graphic be: How to Launch a Multi-Million Business From Scratch

For the color scheme of the graphics, let's try a blue color palette; make sure the graphics appeal to both men and women

Make sure each graphic contains 1 of the 3 pics attached (crop pic as needed); and make sure one of the graphics is all TEXT only.

Target Market(s)

men and women looking to start a business

Industry/Entity Type

Entrepreneurship

Colors
0054AA
0677BA
7BADD7
CADEEF
E8F1F8

Requirements
Must have
• All the text and use the 3 pics provided; one graphic can be all text; Simple, modern design that's easy to read

```html
<!DOCTYPE html>
<html lang="en">
<head>
<meta charset="utf-8">
<title>The Harvest Ledger Circle — Social Graphics</title>
<link href="https://fonts.googleapis.com/css2?family=Alegreya+Sans+SC:wght@800;900&family=Roboto+Condensed:wght@500&display=swap" rel="stylesheet">
<style>
  :root {
    --blue-deep: #0054AA;
    --blue-mid: #0677BA;
    --blue-soft: #7BADD7;
    --blue-pale: #CADEEF;
    --blue-mist: #E8F1F8;
    --ink: #1a1a1a;
    --white: #ffffff;
    --canvas: #ffffff;
  }
  * { margin: 0; padding: 0; box-sizing: border-box; }
  html, body { width: 1200px; height: 819px; overflow: hidden; background: var(--canvas); }
  body { position: relative; font-family: "Alegreya Sans SC", "Trebuchet MS", sans-serif; }

  .tile {
    position: absolute; width: 360px; height: 360px; overflow: hidden;
    background: var(--white);
    box-shadow: 0 1px 4px rgba(0,0,0,0.12);
  }
  .tile--a { left: 29px; top: 35px; background: linear-gradient(160deg, #2fa3e6 0%, var(--blue-mid) 35%, var(--blue-deep) 100%); }
  .tile--b { left: 421px; top: 35px; }
  .tile--c { left: 813px; top: 35px; }
  .tile--d { left: 29px; top: 425px; }
  .tile--e { left: 421px; top: 425px; }
  .tile--f { left: 813px; top: 425px; }

  .abs { position: absolute; }
  .heading { font-weight: 900; line-height: 1; white-space: nowrap; }
  .heading--light { color: var(--white); }
  .heading--dark { color: var(--ink); }
  .heading--blue { color: var(--blue-deep); }
  .accent { color: var(--blue-mid); }
  .centered { left: 0; width: 100%; text-align: center; }

  .cta {
    position: absolute; display: flex; align-items: center; justify-content: center;
    background: var(--blue-mid); color: var(--white);
    font-family: "Roboto Condensed", "Arial Narrow", sans-serif; font-weight: 500;
    border-radius: 999px; border: 2px solid var(--white); white-space: nowrap;
  }

  .photo { position: absolute; }
  .photo--duo { background: linear-gradient(180deg, #3a4a66 0%, #1c2738 55%, #1f4f8f 100%); }
  .photo--pair { background: linear-gradient(180deg, #3b2b26 0%, #d8485f 55%, #1b1b1b 100%); }
  .photo--city { background: linear-gradient(160deg, #0b2a55 0%, #2f8fd6 50%, #0d3a6a 100%); border-radius: 8px; }
  .photo--skyline { background: linear-gradient(180deg, rgba(202,222,239,0) 0%, var(--blue-pale) 40%, var(--blue-mist) 100%); }
  .photo--woman { background: linear-gradient(180deg, #3a2a24 0%, #1d4f8c 45%, #123a6b 100%); border-radius: 60px 60px 0 0; }
  .photo--man { background: linear-gradient(180deg, #3b2a22 0%, #1a2230 45%, #141a24 100%); border-radius: 60px 60px 0 0; }

  .stripe { position: absolute; top: 0; height: 170px; background: var(--blue-deep); opacity: 0.85; }
</style>
</head>
<body>

  <section class="tile tile--a">
    <div class="stripe" style="left:217px;width:30px;"></div>
    <div class="stripe" style="left:257px;width:22px;"></div>
    <div class="stripe" style="left:287px;width:30px;"></div>
    <div class="stripe" style="left:327px;width:33px;"></div>
    <div class="abs heading heading--light" style="left:14px;top:24px;font-size:28px;">The Harvest</div>
    <div class="abs heading heading--light" style="left:14px;top:72px;font-size:28px;">Ledger Circle</div>
    <div class="abs heading heading--light" style="left:17px;top:128px;font-size:23px;line-height:36px;">
      How to<br>Launch a<br>Multi-Million<br>Business<br>From<br>Scratch
    </div>
    <div class="photo photo--duo" role="img" aria-label="Photo of the two course hosts, arms crossed, smiling" style="left:182px;top:88px;width:178px;height:142px;border-radius:40px 40px 0 0;"></div>
    <div class="cta" style="left:181px;top:229px;width:175px;height:47px;font-size:18px;">Sign Up Today!</div>
  </section>

  <section class="tile tile--b">
    <svg class="abs" style="left:0;top:0;" width="360" height="360" viewBox="0 0 360 360" aria-hidden="true">
      <path d="M0 70 C30 92 70 104 130 102 C220 99 300 68 360 48 L360 300 C300 318 220 330 150 340 C80 352 20 350 0 310 Z" fill="var(--blue-mid)"/>
      <path d="M0 230 C60 260 130 270 190 305 L150 340 C80 352 20 350 0 310 Z" fill="var(--blue-deep)" opacity="0.45"/>
    </svg>
    <div class="photo photo--pair" role="img" aria-label="Photo of the two course hosts, a woman in a red dress in front of a smiling man" style="left:190px;top:8px;width:170px;height:352px;border-radius:80px 80px 0 0;"></div>
    <div class="abs heading heading--blue" style="left:32px;top:14px;font-size:25px;line-height:36px;">The Harvest<br>Ledger Circle</div>
    <div class="abs heading heading--light" style="left:18px;top:108px;font-size:23px;line-height:34px;">
      How to<br>Launch a<br>Multi-Million<br>Business<br>From<br>Scratch
    </div>
    <div class="cta" style="left:181px;top:308px;width:175px;height:47px;font-size:18px;">Sign Up Today!</div>
  </section>

  <section class="tile tile--c">
    <div class="abs heading heading--dark centered" style="top:20px;font-size:24px;">The Harvest Ledger Circle</div>
    <div class="abs heading heading--dark centered" style="top:59px;font-size:23px;">How to Launch a</div>
    <div class="abs heading accent centered" style="top:92px;font-size:23px;">Multi-Million Business</div>
    <div class="abs heading heading--blue centered" style="top:126px;font-size:23px;">From Scratch</div>
    <div class="abs" style="left:27px;top:211px;width:306px;height:109px;border-radius:36px;background:linear-gradient(120deg,var(--blue-mid),var(--blue-deep));"></div>
    <div class="photo photo--duo" role="img" aria-label="Photo of the two course hosts, arms crossed, smiling" style="left:87px;top:163px;width:186px;height:132px;border-radius:40px 40px 0 0;"></div>
    <div class="cta" style="left:93px;top:296px;width:174px;height:47px;font-size:18px;">Sign Up Today!</div>
  </section>

  <section class="tile tile--d">
    <div class="abs heading heading--dark centered" style="top:11px;font-size:24px;">The Harvest Ledger Circle</div>
    <div class="abs heading heading--dark centered" style="top:50px;font-size:23px;">How to Launch a</div>
    <div class="abs heading accent centered" style="top:83px;font-size:23px;">Multi-Million Business</div>
    <div class="abs heading heading--blue centered" style="top:116px;font-size:23px;">From Scratch</div>
    <div class="abs" style="left:203px;top:167px;width:157px;height:33px;background:var(--blue-mid);border-radius:10px 0 0 0;"></div>
    <div class="abs" style="left:0;top:313px;width:155px;height:33px;background:var(--blue-deep);border-radius:0 16px 16px 0;"></div>
    <div class="cta" style="left:20px;top:154px;width:38px;height:147px;font-size:15px;border:none;">
      <span style="display:block;transform:rotate(-90deg);">Sign Up Today!</span>
    </div>
    <div class="photo photo--city" role="img" aria-label="Photo looking up at glass skyscrapers against a blue sky" style="left:82px;top:167px;width:115px;height:144px;"></div>
    <div class="photo photo--duo" role="img" aria-label="Photo of the two course hosts standing together indoors" style="left:158px;top:194px;width:123px;height:152px;border:3px solid var(--white);border-radius:8px;"></div>
  </section>

  <section class="tile tile--e">
    <div class="photo photo--skyline" role="img" aria-label="Faded photo of glass office towers" style="left:0;top:160px;width:360px;height:200px;"></div>
    <div class="abs heading heading--dark centered" style="top:40px;font-size:24px;">The Harvest Ledger Circle</div>
    <div class="abs heading heading--dark centered" style="top:85px;font-size:23px;">How to Launch a</div>
    <div class="abs heading accent centered" style="top:118px;font-size:23px;">Multi-Million Business</div>
    <div class="abs heading heading--blue centered" style="top:151px;font-size:23px;">From Scratch</div>
    <div class="cta" style="left:106px;top:203px;width:148px;height:38px;font-size:15px;">Sign Up Today!</div>
  </section>

  <section class="tile tile--f">
    <div class="abs heading heading--dark centered" style="top:23px;font-size:24px;">The Harvest Ledger Circle</div>
    <div class="abs heading heading--dark centered" style="top:66px;font-size:23px;">How to Launch a</div>
    <div class="abs heading accent centered" style="top:99px;font-size:23px;">Multi-Million Business</div>
    <div class="abs heading heading--blue centered" style="top:132px;font-size:23px;">From Scratch</div>
    <div class="photo photo--woman" role="img" aria-label="Photo of the female host in a blue jacket, smiling" style="left:0;top:151px;width:126px;height:209px;"></div>
    <div class="photo photo--man" role="img" aria-label="Photo of the male host in a black turtleneck, arms crossed" style="left:228px;top:148px;width:132px;height:212px;"></div>
    <div class="cta" style="left:94px;top:185px;width:147px;height:41px;font-size:15px;">Sign Up Today!</div>
  </section>

</body>
</html>
```